4th Generation Family Business Needs a New Card Design!

We are a family owned 4th Generation company. We are based in the Sydney, Australia area and we are desperately in need of a more modern and classy card. We are monumental masons who design, supply & erect lasting memorials throughout cemeteries in Sydney. Our customers are normally in a period of grieving. I have attached logo files that will need to be implemented on the card. Company was established 1935. Australian Owned and Operated. Card needs to be designed to PIXO.com specification.

Target Market(s)

Our target market is based upon people that a grieving for family members that have passed away. We also deal with alot of companies that own and operate cemeteries.

Industry/Entity Type

Business

Contact Information for Business Card

Simon Harcourt, Operations Manager, 0417293086, simon@harcourtmemorials.com.au
Lewis Harcourt, Director, 0491630572, lewis@harcourtmemorials.com.au
Phone # 02 9561 3048
Website: www.harcourtmemorials.com.au
Address: Suite 17, 8 Palfrey Lane, West Carlow, Sydney NSW 2156

Font styles to use
Serif
Decorative
Script

Requirements
Must have
• Would like to see the logo nicely implemented with a modern design. Embossed lettering would be a nice additive.

```html
<!DOCTYPE html>
<html lang="en">
<head>
<meta charset="utf-8">
<title>Harcourt Memorials – Business Card</title>
<link href="https://fonts.googleapis.com/css2?family=Roboto:wght@400;500;700&display=swap" rel="stylesheet">
<style>
  :root {
    --stage: #232323;
    --card-black: #111111;
    --card-black-edge: #1c1c1c;
    --gold: #ecc24b;
    --gold-deep: #e7b93f;
    --ink: #141414;
    --white: #ffffff;
    --silver: #9a9a9a;
    --silver-dim: #5e5e5e;
  }
  * { box-sizing: border-box; margin: 0; padding: 0; }
  html, body {
    width: 1200px; height: 900px; overflow: hidden;
    background: var(--stage);
    font-family: "Roboto", Arial, sans-serif;
  }
  .canvas {
    position: relative; width: 1200px; height: 900px;
    display: flex; align-items: center; justify-content: center; gap: 60px;
  }
  .card {
    position: relative; width: 525px; height: 300px;
    border-radius: 3px; overflow: hidden;
    box-shadow: 0 18px 40px rgba(0,0,0,.55);
  }

  /* Front */
  .card-front { display: flex; }
  .front-brand {
    width: 40%; background: linear-gradient(160deg, var(--card-black-edge), var(--card-black));
    display: flex; flex-direction: column; align-items: center; justify-content: center; gap: 14px;
  }
  .front-details {
    width: 60%; background: linear-gradient(170deg, var(--gold), var(--gold-deep));
    padding: 30px 26px 26px 28px;
    display: flex; flex-direction: column; justify-content: space-between;
    color: var(--ink);
  }
  .brand-mark { display: flex; align-items: center; gap: 8px; }
  .brand-square { width: 12px; height: 12px; background: var(--silver); }
  .brand-name {
    color: var(--silver); font-weight: 500; letter-spacing: 2px;
    font-size: 17px; line-height: 1.15; text-transform: uppercase;
  }
  .brand-web { color: var(--silver-dim); font-size: 8.5px; letter-spacing: .3px; }

  .person-name { font-size: 25px; font-weight: 700; line-height: 1.1; }
  .person-name .surname { color: var(--white); }
  .person-role { font-size: 12.5px; margin-top: 6px; letter-spacing: .6px; }

  .contact-title { font-size: 11px; font-weight: 700; text-transform: uppercase; margin-bottom: 5px; }
  .contact-line { font-size: 10.5px; line-height: 1.5; }

  /* Back */
  .card-back {
    background: linear-gradient(160deg, var(--card-black-edge), var(--card-black));
    display: flex; align-items: center; justify-content: center;
  }
  .card-back .brand-name { font-size: 24px; letter-spacing: 3px; }
  .card-back .brand-square { width: 16px; height: 16px; }
</style>
</head>
<body>
<main class="canvas">
  <section class="card card-front" aria-label="Business card front">
    <div class="front-brand">
      <div class="brand-mark">
        <span class="brand-square"></span>
        <span class="brand-name">Harcourt Memorials</span>
      </div>
      <span class="brand-web">www.harcourtmemorials.com.au</span>
    </div>
    <div class="front-details">
      <div class="person">
        <h1 class="person-name">Simon <span class="surname">Harcourt</span></h1>
        <p class="person-role">Operation Manager (0417293086)</p>
      </div>
      <div class="contact">
        <h2 class="contact-title">Contact</h2>
        <p class="contact-line">02 9561 3048</p>
        <p class="contact-line">simon@harcourtmemorials.com.au</p>
        <p class="contact-line">Suite 17, 8 Palfrey Lane, West Carlow, Sydney NSW 2156</p>
      </div>
    </div>
  </section>

  <section class="card card-back" aria-label="Business card back">
    <div class="brand-mark">
      <span class="brand-square"></span>
      <span class="brand-name">Harcourt Memorials</span>
    </div>
  </section>
</main>
</body>
</html>
```